Business Card - connecting 2 souls and beggining the journey of self discovery

Logo on the front
with tag line

On the back list of services and contact details

Seminars
workshops
Coaching
podcasts

Darren Whitlow
Health & Wellbeing Life Coach
0491 372 615
darren@brightcoreliving.example
brightcoreliving.example

Industry/Entity Type

Life Coaching

Contact Information for Business Card

I like the use of colour from the logo to be used. I'm not a fan of white.

Requirements
Must have
• My tagline: The journey home starts with you
Nice to have
• Use of colour that is in the mind body soul logo

```html
<!DOCTYPE html>
<html lang="en">
<head>
<meta charset="utf-8">
<title>Brightcore Living – Business Card</title>
<link rel="stylesheet" href="https://fonts.googleapis.com/css2?family=Open+Sans:wght@400;600;700&display=swap">
<style>
  :root {
    --page-bg: #d8d3cb;
    --card-frost: #ebe9e5;
    --card-frost-edge: #dedbd6;
    --panel-dark: #4a4a4d;
    --text-heading: #5a5a5c;
    --text-body: #3f3f42;
    --text-light: #f1f1f1;
    --text-muted: #c9c9cc;
    --accent-red: #d3372f;
    --accent-green: #3b9d4b;
    --accent-purple: #6b3e90;
    --accent-orange: #e9962b;
  }
  * { margin: 0; padding: 0; box-sizing: border-box; }
  html, body {
    width: 1200px;
    height: 969px;
    overflow: hidden;
    background: var(--page-bg);
    font-family: "Open Sans", Arial, sans-serif;
  }
  .card {
    position: absolute;
    left: 100px;
    top: 202px;
    width: 1000px;
    height: 565px;
    background: linear-gradient(135deg, var(--card-frost) 0%, var(--card-frost-edge) 100%);
    border: 1px solid #f6f5f3;
    box-shadow: 0 14px 40px rgba(0,0,0,0.18);
    overflow: hidden;
  }
  .card-shapes {
    position: absolute;
    inset: 0;
  }
  .brand-mark {
    position: absolute;
    left: 174px;
    top: 43px;
    width: 148px;
    height: 148px;
    border-radius: 50%;
    background: var(--accent-purple);
  }
  .brand-name {
    position: absolute;
    left: 36px;
    top: 226px;
    font-size: 34px;
    font-weight: 400;
    color: var(--text-heading);
    letter-spacing: -0.5px;
  }
  .tagline {
    position: absolute;
    left: 36px;
    top: 272px;
    font-size: 24px;
    font-weight: 700;
    color: var(--text-heading);
  }
  .contact-list {
    position: absolute;
    left: 44px;
    top: 372px;
    list-style: none;
  }
  .contact-item {
    display: flex;
    align-items: center;
    height: 31px;
    font-size: 22px;
    color: var(--text-body);
  }
  .contact-icon {
    width: 20px;
    height: 20px;
    margin-right: 10px;
    flex: none;
  }
  .services {
    position: absolute;
    left: 40px;
    top: 479px;
    font-size: 21px;
    color: var(--text-body);
    display: flex;
    align-items: center;
  }
  .service-dot {
    display: inline-block;
    width: 7px;
    height: 7px;
    border-radius: 50%;
    background: var(--accent-green);
    margin: 0 7px;
  }
  .person {
    position: absolute;
    left: 925px;
    top: 282px;
    transform: translate(-50%, -50%) rotate(-90deg);
    white-space: nowrap;
    text-align: left;
  }
  .person-name {
    font-size: 29px;
    font-weight: 700;
    color: var(--text-light);
    letter-spacing: 1px;
    line-height: 38px;
  }
  .person-role {
    font-size: 22px;
    font-weight: 600;
    color: var(--text-muted);
    letter-spacing: 0.8px;
    line-height: 32px;
  }
</style>
</head>
<body>
  <div class="card">
    <svg class="card-shapes" width="1000" height="565" viewBox="0 0 1000 565" aria-hidden="true">
      <defs>
        <clipPath id="band-top"><rect x="0" y="0" width="1000" height="172"/></clipPath>
        <clipPath id="band-middle"><rect x="0" y="172" width="1000" height="236"/></clipPath>
        <clipPath id="band-bottom"><rect x="0" y="408" width="1000" height="157"/></clipPath>
      </defs>
      <path class="side-panel" d="M707 0 Q959 282.5 707 565 L1000 565 L1000 0 Z" fill="var(--panel-dark)"/>
      <path d="M707 0 Q959 282.5 707 565" fill="none" stroke="var(--accent-red)" stroke-width="12" clip-path="url(#band-top)"/>
      <path d="M707 0 Q959 282.5 707 565" fill="none" stroke="var(--accent-green)" stroke-width="12" clip-path="url(#band-middle)"/>
      <path d="M707 0 Q959 282.5 707 565" fill="none" stroke="var(--accent-purple)" stroke-width="12" clip-path="url(#band-bottom)"/>
      <path d="M699 0 Q951 282.5 699 565" fill="none" stroke="#ffffff" stroke-width="2" opacity="0.8"/>
      <line x1="820" y1="170" x2="832" y2="174" stroke="#ffffff" stroke-width="2"/>
      <line x1="822" y1="406" x2="834" y2="402" stroke="#ffffff" stroke-width="2"/>
    </svg>

    <div class="brand-mark"></div>
    <h1 class="brand-name">Brightcore Living</h1>
    <p class="tagline">The journey home starts with you</p>

    <ul class="contact-list">
      <li class="contact-item">
        <svg class="contact-icon" viewBox="0 0 20 20" aria-hidden="true">
          <path d="M3 7 Q10 1 17 7 L15 9 L13 7.5 L7 7.5 L5 9 Z" fill="var(--accent-green)"/>
          <rect x="5" y="10" width="10" height="7" rx="1.5" fill="var(--accent-green)"/>
        </svg>
        <span>0491 372 615</span>
      </li>
      <li class="contact-item">
        <svg class="contact-icon" viewBox="0 0 20 20" aria-hidden="true">
          <rect x="2" y="5" width="16" height="11" rx="1" fill="var(--accent-green)"/>
          <path d="M2.5 5.5 L10 11 L17.5 5.5" fill="none" stroke="#ffffff" stroke-width="1.4"/>
        </svg>
        <span>darren@brightcoreliving.example</span>
      </li>
      <li class="contact-item">
        <svg class="contact-icon" viewBox="0 0 20 20" aria-hidden="true">
          <circle cx="10" cy="10" r="8" fill="var(--accent-green)"/>
          <ellipse cx="10" cy="10" rx="3.5" ry="8" fill="none" stroke="#ffffff" stroke-width="1.2"/>
          <line x1="2" y1="10" x2="18" y2="10" stroke="#ffffff" stroke-width="1.2"/>
        </svg>
        <span>www.brightcoreliving.example</span>
      </li>
    </ul>

    <p class="services">
      <span>Seminars</span><span class="service-dot"></span><span>Workshops</span><span class="service-dot"></span><span>Coaching</span><span class="service-dot"></span><span>Podcasts</span>
    </p>

    <div class="person">
      <p class="person-name">DARREN WHITLOW</p>
      <p class="person-role">HEALTH &amp; WELLBEING LIFE COACH</p>
    </div>
  </div>
</body>
</html>
```